Website for my law practice

I am a solo practitioner, who specializes in family law and estate planning in Massachusetts. I need to re-do my website, as it is outdated. I like the idea of a nontraditional law firm website. My website address is: doloresquintanalaw.com. I would like to retain my logo in the green color, as part of the new website. I have uploaded my logo below.

My hourly rate has changed from what is listed on my current website. My new hourly rate is $385.00. Please use this hourly rate when creating the website.

Good morning,

I have reviewed the designs submitted so far. I am happy that the "dq" logo in the green color is part of each of the designs submitted. I am also happy that the standard items seen in law firm websites, such as the scales of justice, etc. were not incorporated. Although the green logo is great, I do not think rest of the website has to have the same green color throughout. Additionally, I was hoping for something more creative, to make the website standout and not the stock web designs you see everyday. Please incorporate more unique images if you can. For example of what I mean, please look at this website: https://www.rosalindfenwicklaw.com

```html
<!DOCTYPE html>
<html lang="en">
<head>
<meta charset="utf-8">
<title>Dolores Quintana, Attorney at Law</title>
<link href="https://fonts.googleapis.com/css2?family=Josefin+Sans:wght@400;600;700&family=Poppins:wght@300;400;500&display=swap" rel="stylesheet">
<style>
:root{
  --green:#4b8b35;
  --green-bright:#5aa83e;
  --green-soft:#6f9a5f;
  --mint:#e4f3dd;
  --ink:#1d1d1d;
  --text:#333;
  --grey-bg:#e8e8e8;
  --charcoal:#2a2a2a;
  --black:#000;
  --white:#fff;
  --star:#f29a1c;
}
*{box-sizing:border-box;margin:0;padding:0}
html,body{width:1200px;height:4000px;overflow:hidden}
body{position:relative;font-family:"Josefin Sans",sans-serif;color:var(--ink);background:var(--white)}
.abs{position:absolute}

/* header */
.site-header{position:absolute;left:0;top:0;width:1200px;height:120px;border-top:4px solid var(--green);background:var(--white)}
.brand{position:absolute;left:112px;top:36px;display:flex;align-items:center;gap:10px;color:var(--green);font-size:15px;font-weight:600;line-height:1.1}
.brand-dot{width:46px;height:46px;border-radius:50%;border:5px solid var(--green)}
.main-nav{position:absolute;left:387px;top:66px;display:flex;gap:35px;font-family:Poppins,sans-serif;font-size:16px;color:var(--text)}
.main-nav .active{color:var(--green);border-bottom:1px solid var(--green)}
.header-phone{position:absolute;left:675px;top:15px;display:flex;align-items:center;gap:12px;font-family:Poppins,sans-serif;font-weight:500;font-size:17px}
.icon-circle{width:38px;height:38px;border-radius:50%;background:var(--green);display:flex;align-items:center;justify-content:center;flex:none}
.btn{display:inline-flex;align-items:center;justify-content:center;background:var(--green);color:var(--white);font-weight:700;border-radius:30px;letter-spacing:.5px}
.header-cta{position:absolute;left:888px;top:14px;width:200px;height:38px;font-size:15px}

/* hero */
.hero{position:absolute;left:0;top:120px;width:1200px;height:630px}
.hero-title{position:absolute;left:110px;top:140px;color:var(--white);font-size:39px;font-weight:700;line-height:1.2;letter-spacing:1px}
.hero-text{position:absolute;left:110px;top:245px;width:440px;color:var(--white);font-family:Poppins,sans-serif;font-weight:300;font-size:16.5px;line-height:32px}
.hero-cta{position:absolute;left:110px;top:355px;width:326px;height:46px;font-size:17px}

/* section heading */
.section-title{position:absolute;left:0;width:1200px;text-align:center;font-size:33px;font-weight:700;letter-spacing:1px;color:var(--ink)}
.section-title .accent{color:var(--green)}

.services-intro{position:absolute;left:180px;top:890px;width:840px;text-align:center;font-size:18px;line-height:27px;color:var(--ink)}
.service-card{position:absolute;top:978px;width:481px;height:376px;border-radius:24px;overflow:hidden}
.service-card .label{position:absolute;left:30px;bottom:24px;color:var(--white);font-size:28px;font-weight:700;letter-spacing:.5px}
.service-card .go{position:absolute;right:32px;bottom:22px;width:32px;height:32px}

/* about */
.about-kicker{position:absolute;left:108px;top:1602px;color:var(--green);font-size:31px;font-weight:700}
.about-name{position:absolute;left:108px;top:1640px;font-size:31px;font-weight:700;letter-spacing:.5px}
.about-text{position:absolute;left:111px;top:1690px;width:450px;font-size:15.5px;line-height:26px;color:#222}
.about-text p+p{margin-top:10px}
.about-cta{position:absolute;left:111px;top:1896px;width:155px;height:44px;font-size:17px}

/* reviews */
.review-card{position:absolute;top:2205px;width:318px;height:276px;border:1px solid #ddd;border-radius:14px;background:var(--white)}
.review-card.featured{border:2px solid var(--green);box-shadow:0 4px 14px rgba(0,0,0,.12)}
.review-card .avatar{position:absolute;left:20px;top:18px;width:68px;height:68px;border-radius:50%;background:linear-gradient(135deg,#8a6a55,#3b2f29)}
.review-card .who{position:absolute;left:103px;top:24px;font-weight:700;font-size:17px}
.review-card .stars{position:absolute;left:101px;top:44px;color:var(--star);font-size:15px;letter-spacing:-1px}
.review-card .when{position:absolute;left:103px;top:72px;font-size:12px;font-weight:600}
.review-card .body{position:absolute;left:30px;top:112px;width:258px;font-size:12px;line-height:23px;color:var(--text)}

/* contact */
.contact-bg{position:absolute;left:0;top:2572px;width:1200px;height:900px;background:var(--grey-bg)}
.contact-info{position:absolute;top:2717px;display:flex;align-items:center;gap:16px;font-size:16px;line-height:22px}
.contact-info .icon-circle{width:54px;height:54px}
.field{position:absolute;height:62px;border:1px solid #bbb;border-radius:31px;background:var(--white);padding:21px 20px;font-size:18px;color:var(--text)}
.field.message{height:140px;border-radius:26px}
.captcha{position:absolute;left:150px;top:3135px;width:160px;height:56px;background:linear-gradient(90deg,#b9dcdc,#a8cfd4)}
.submit{position:absolute;left:668px;top:3140px;width:128px;height:44px;font-size:17px;border:2px solid var(--white);box-shadow:0 0 0 1px var(--green)}
.captcha-note{position:absolute;left:330px;top:3208px;font-size:12px;color:var(--text);line-height:22px}
.captcha-note a{color:var(--green);text-decoration:none}

/* footer */
.footer-brand{position:absolute;left:430px;top:3480px;display:flex;align-items:center;gap:16px;color:var(--green);font-size:24px;font-weight:600;line-height:1.15}
.footer-brand .brand-dot{width:88px;height:88px;border-width:8px}
.footer-rule{position:absolute;left:112px;top:3625px;width:976px;height:1px;background:#2b2b2b}
.foot-col{position:absolute;top:3672px;color:var(--white)}
.foot-col h3{color:var(--green-bright);font-size:25px;font-weight:700;letter-spacing:.5px;margin-bottom:12px}
.foot-col li{list-style:none;font-size:18px;line-height:30px}
.foot-col p{font-size:17px;line-height:29px}
.news-input{width:334px;height:44px;border-radius:22px;background:var(--charcoal);color:#ddd;font-size:15px;font-weight:600;padding:15px 20px;margin-top:6px}
.news-btn{margin-top:18px;width:128px;height:44px;font-size:17px}
.copyright{position:absolute;left:0;top:3948px;width:1200px;text-align:center;color:var(--white);font-size:14px}
</style>
</head>
<body>

<header class="site-header">
  <div class="brand"><span class="brand-dot"></span><span>Dolores Quintana<br>Attorney at Law</span></div>
  <div class="header-phone"><span class="icon-circle"><svg width="16" height="16" viewBox="0 0 24 24"><path fill="#fff" d="M6.6 10.8a15 15 0 0 0 6.6 6.6l2.2-2.2c.3-.3.7-.4 1-.2 1.1.4 2.3.6 3.6.6.6 0 1 .4 1 1V20c0 .6-.4 1-1 1A17 17 0 0 1 3 4c0-.6.4-1 1-1h3.5c.6 0 1 .4 1 1 0 1.3.2 2.5.6 3.6.1.3 0 .7-.2 1z"/></svg></span>978-555-0143</div>
  <a class="btn header-cta">FREE CONSULTATION</a>
  <nav class="main-nav"><span class="active">Home</span><span>Family Law</span><span>Estate Planning</span><span>About</span><span>Location</span><span>Contact</span><span>FAQ</span></nav>
</header>

<section class="hero">
  <svg class="abs" style="left:0;top:0" width="1200" height="630" viewBox="0 0 1200 630">
    <defs>
      <linearGradient id="heroSky" x1="0" y1="0" x2="0" y2="1">
        <stop offset="0" stop-color="#6f7f8f"/><stop offset=".45" stop-color="#8d949a"/><stop offset=".75" stop-color="#7b776e"/><stop offset="1" stop-color="#6a6658"/>
      </linearGradient>
    </defs>
    <path role="img" aria-label="City skyline with a cable-stayed bridge" d="M0 0H1200V490Q600 760 0 490Z" fill="url(#heroSky)"/>
    <path d="M90 520Q600 720 1120 500Q600 760 90 520Z" fill="var(--green-soft)"/>
  </svg>
  <h1 class="hero-title">EMPATHY AND EXPERTISE<br>IN FAMILY LAW MATTERS</h1>
  <p class="hero-text">Dolores Quintana is a Solo Practitioner focusing her practice on matters pertaining to family law and estate planning.</p>
  <a class="btn hero-cta">FREE 30-MINUTE CONSULTATION</a>
</section>

<h2 class="section-title" style="top:843px"><span class="accent">OUR</span> SERVICES</h2>
<p class="services-intro">Dolores Quintana is a Solo Practitioner focusing her practice on matters pertaining to family law and estate planning.</p>

<a class="service-card" style="left:112px">
  <div role="img" aria-label="Family walking together on a beach" class="abs" style="inset:0;background:linear-gradient(180deg,#aab8c4 0%,#8a8a84 55%,#5d5a55 100%)"></div>
  <span class="label">Family Law</span>
  <svg class="go" viewBox="0 0 32 32"><circle cx="16" cy="16" r="14" fill="none" stroke="#fff" stroke-width="2"/><path d="M10 16h11M17 11l5 5-5 5" fill="none" stroke="#fff" stroke-width="2"/></svg>
</a>
<a class="service-card" style="left:607px">
  <div role="img" aria-label="Older couple reviewing documents with an advisor" class="abs" style="inset:0;background:linear-gradient(180deg,#d9d6ce 0%,#8d8a86 55%,#4a4c55 100%)"></div>
  <span class="label">Estate Planning</span>
  <svg class="go" viewBox="0 0 32 32"><circle cx="16" cy="16" r="14" fill="none" stroke="#fff" stroke-width="2"/><path d="M10 16h11M17 11l5 5-5 5" fill="none" stroke="#fff" stroke-width="2"/></svg>
</a>

<section class="about">
  <svg class="abs" style="left:0;top:1420px" width="1200" height="620" viewBox="0 0 1200 620">
    <path d="M0 130Q600 -90 1200 130V620H0Z" fill="var(--mint)"/>
    <rect x="825" y="5" width="40" height="130" fill="var(--green)"/>
    <circle cx="838" cy="356" r="157" fill="none" stroke="var(--green)" stroke-width="22"/>
    <circle cx="838" cy="356" r="140" fill="var(--white)"/>
    <circle role="img" aria-label="Portrait of Dolores Quintana" cx="838" cy="356" r="130" fill="#9a9a9a"/>
  </svg>
  <div class="about-kicker">ABOUT</div>
  <div class="about-name">DOLORES QUINTANA</div>
  <div class="about-text">
    <p>Dolores is a graduate of Harborview University in Harborview, Massachusetts. She received her Bachelors of Science degree in Criminal Justice and a minor in Political Science in 1993. While attending Harborview, Dolores was an Eleanor Whitcombe Scholar, graduating from the University Magna Cum Laude.</p>
    <p>Dolores obtained her Juris Doctor from Kestrel University Law School in Harborview, Massachusetts in 1999.</p>
  </div>
  <a class="btn about-cta">READ MORE</a>
</section>

<h2 class="section-title" style="top:2120px"><span class="accent">CLIENTS</span> REVIEWS</h2>
<article class="review-card" style="left:110px"><div class="avatar" role="img" aria-label="Reviewer photo"></div><div class="who">Samuel</div><div class="stars">★★★★★</div><div class="when">2min.ago</div><p class="body">Lorem ipsum dolor sit amet, consectetur adipiscing elit, sed do eiusmod tempor incididunt ut labore et dolore magna aliqua. Quis ipsum suspendisse ultrices gravida. Risus commodo viverra maecenas accumsan lacus vel facilisis.</p></article>
<article class="review-card featured" style="left:438px"><div class="avatar" role="img" aria-label="Reviewer photo"></div><div class="who">Emma</div><div class="stars">★★★★★</div><div class="when">2min.ago</div><p class="body">Lorem ipsum dolor sit amet, consectetur adipiscing elit, sed do eiusmod tempor incididunt ut labore et dolore magna aliqua. Quis ipsum suspendisse ultrices gravida. Risus commodo viverra maecenas accumsan lacus vel facilisis.</p></article>
<article class="review-card" style="left:767px"><div class="avatar" role="img" aria-label="Reviewer photo"></div><div class="who">Scott</div><div class="stars">★★★★★</div><div class="when">2min.ago</div><p class="body">Lorem ipsum dolor sit amet, consectetur adipiscing elit, sed do eiusmod tempor incididunt ut labore et dolore magna aliqua. Quis ipsum suspendisse ultrices gravida. Risus commodo viverra maecenas accumsan lacus vel facilisis.</p></article>

<div class="contact-bg"></div>
<h2 class="section-title" style="top:2647px"><span class="accent">CONTACT</span> US</h2>
<div class="contact-info" style="left:157px"><span class="icon-circle"><svg width="20" height="24" viewBox="0 0 20 24"><path fill="#fff" d="M10 0a8 8 0 0 0-8 8c0 6 8 16 8 16s8-10 8-16a8 8 0 0 0-8-8zm0 11a3 3 0 1 1 0-6 3 3 0 0 1 0 6z"/></svg></span><span>42 Linden Street Harlow,<br>MA 01990</span></div>
<div class="contact-info" style="left:483px"><span class="icon-circle"><svg width="20" height="20" viewBox="0 0 24 24"><path fill="#fff" d="M6.6 10.8a15 15 0 0 0 6.6 6.6l2.2-2.2c.3-.3.7-.4 1-.2 1.1.4 2.3.6 3.6.6.6 0 1 .4 1 1V20c0 .6-.4 1-1 1A17 17 0 0 1 3 4c0-.6.4-1 1-1h3.5c.6 0 1 .4 1 1 0 1.3.2 2.5.6 3.6.1.3 0 .7-.2 1z"/></svg></span><span>978-555-0143</span></div>
<div class="contact-info" style="left:723px"><span class="icon-circle"><svg width="24" height="18" viewBox="0 0 24 18"><rect x="1" y="1" width="22" height="16" rx="2" fill="#fff"/><path d="M2 3l10 7 10-7" fill="none" stroke="#4b8b35" stroke-width="2"/></svg></span><span>dolores@quintanafamilylaw.net</span></div>

<div class="field" style="left:144px;top:2820px;width:448px">Name</div>
<div class="field" style="left:607px;top:2820px;width:448px">Phone</div>
<div class="field" style="left:144px;top:2897px;width:448px">Email</div>
<div class="field" style="left:607px;top:2897px;width:448px">Subject</div>
<div class="field message" style="left:144px;top:2975px;width:911px">Message</div>
<div class="captcha" role="img" aria-label="Security code"></div>
<div class="field" style="left:321px;top:3132px;width:333px">Code</div>
<a class="btn submit">SUBMIT</a>
<p class="captcha-note">(Please enter the code above. Text is not case sensitive.)<br><a>Click here to try another code.</a></p>

<footer>
  <svg class="abs" style="left:0;top:3340px" width="1200" height="660" viewBox="0 0 1200 660">
    <path d="M0 140Q600 -110 1200 140V660H0Z" fill="var(--black)"/>
    <path d="M90 112Q600 -90 1110 112Q600 -70 90 112Z" fill="var(--green-soft)"/>
  </svg>
  <div class="footer-brand"><span class="brand-dot"></span><span>Dolores Quintana<br>Attorney at Law</span></div>
  <div class="footer-rule"></div>
  <div class="foot-col" style="left:171px"><h3>QUICK LINKS</h3><ul><li>Home</li><li>Family Law</li><li>Estate Planning</li><li>About</li><li>Location</li><li>Contact</li><li>FAQ</li></ul></div>
  <div class="foot-col" style="left:402px"><h3>CONTACT US</h3><p>42 Linden Street Harlow,<br>MA 01990</p><p style="margin-top:4px">Phone: 978-555-0143</p><p style="margin-top:4px">Fax: 978-555-0144</p><p style="margin-top:4px;font-size:15px">dolores@quintanafamilylaw.net</p></div>
  <div class="foot-col" style="left:695px"><h3>NEWSLETTER</h3><div class="news-input">Enter Your Email</div><a class="btn news-btn">SUBMIT</a></div>
  <p class="copyright">© 2025 Dolores Quintanalaw | All rights reserved</p>
</footer>

</body>
</html>
```